Business Card Design (NEW FILES)

ATTENTION: New vector files are available. Please update your design to reflect/use the new (better resolution) logo images.

Seeking a unique and professional business card design for a commercial drone photography/videography business. The layout should feature
the logo (attached) and include the following information:
Owen Tarrick
614-502-7738
www.skylarkreelworks.example
NRD Certified Remote Pilot

Owen Tarrick

```html
<!DOCTYPE html>
<html lang="en">
<head>
<meta charset="utf-8">
<title>Skylark Reelworks – Business Card</title>
<link rel="stylesheet" href="https://fonts.googleapis.com/css2?family=Montserrat:wght@700;800&family=Open+Sans:wght@400;600&display=swap">
<style>
  :root {
    --stage: #222222;
    --paper: #ffffff;
    --orange: #ec8a52;
    --orange-deep: #e0773c;
    --navy: #1b2150;
  }
  * { box-sizing: border-box; margin: 0; padding: 0; }
  html, body { width: 1200px; height: 780px; overflow: hidden; background: var(--stage); }
  .canvas {
    width: 1200px; height: 780px;
    display: flex; flex-direction: column; align-items: center; justify-content: center; gap: 36px;
  }
  .card {
    position: relative; width: 600px; height: 343px;
    border-radius: 26px; overflow: hidden;
    box-shadow: 0 10px 28px rgba(0,0,0,.55);
  }

  /* Back side */
  .card--back { background: var(--orange); }
  .back-pattern {
    position: absolute; inset: 0;
    background: radial-gradient(circle at 50% 40%, #f09a62 0%, var(--orange) 55%, var(--orange-deep) 100%);
  }
  .back-brand {
    position: absolute; right: 70px; bottom: 78px;
    display: flex; align-items: center; gap: 8px;
    font-family: "Open Sans", sans-serif; font-weight: 600; font-size: 17px; color: var(--navy);
  }
  .brand-dot { width: 12px; height: 12px; border-radius: 50%; background: var(--navy); }

  /* Front side */
  .card--front { background: var(--paper); border-bottom: 5px solid var(--orange); }
  .front-brand {
    position: absolute; left: 46px; top: 28px; bottom: 28px;
    display: flex; flex-direction: column; align-items: center; gap: 12px;
  }
  .front-brand__name {
    writing-mode: vertical-rl;
    font-family: "Open Sans", sans-serif; font-weight: 600; font-size: 40px;
    letter-spacing: 1px; color: var(--navy); line-height: 1;
  }
  .front-brand .brand-dot { width: 26px; height: 26px; background: var(--orange); }

  .contact {
    position: absolute; right: 34px; top: 74px;
    text-align: right; color: var(--navy);
    font-family: "Open Sans", sans-serif;
  }
  .contact__name {
    font-family: "Montserrat", sans-serif; font-weight: 800; font-size: 30px; line-height: 1.05;
  }
  .contact__first { color: var(--orange); }
  .contact__last { color: var(--navy); }
  .contact__role { font-weight: 600; font-size: 15px; margin-top: 2px; }
  .contact__creds { font-weight: 600; font-size: 14.5px; line-height: 1.45; margin-top: 22px; }
  .contact__lines { margin-top: 18px; font-weight: 600; font-size: 14.5px; line-height: 1.6; }
  .contact__line { display: flex; align-items: center; justify-content: flex-end; gap: 8px; }
  .contact__line svg { width: 14px; height: 14px; flex: none; }
  .contact__line--web { margin-right: 22px; }

  .name-tab {
    position: absolute; right: 0; top: 70px; width: 16px; height: 56px; background: var(--orange);
  }
</style>
</head>
<body>
<main class="canvas">
  <section class="card card--back" aria-label="Card back">
    <div class="back-pattern" role="img" aria-label="Repeating embossed pattern of small aerial drones on orange"></div>
    <div class="back-brand"><span class="brand-dot"></span>Skylark Reelworks</div>
  </section>

  <section class="card card--front" aria-label="Card front">
    <div class="front-brand">
      <span class="brand-dot"></span>
      <span class="front-brand__name">Skylark Reelworks</span>
    </div>

    <span class="name-tab"></span>

    <div class="contact">
      <p class="contact__name"><span class="contact__first">Owen</span> <span class="contact__last">Tarrick</span></p>
      <p class="contact__role">Owner</p>
      <p class="contact__creds">NRD Certified Remote Pilot<br>Fully Insured</p>
      <div class="contact__lines">
        <p class="contact__line">614-502-7738
          <svg viewBox="0 0 24 24" aria-hidden="true"><path fill="#ec8a52" d="M6.6 10.8a15.1 15.1 0 0 0 6.6 6.6l2.2-2.2c.3-.3.7-.4 1-.2 1.1.4 2.3.6 3.6.6.6 0 1 .4 1 1V20c0 .6-.4 1-1 1A17 17 0 0 1 3 4c0-.6.4-1 1-1h3.5c.6 0 1 .4 1 1 0 1.3.2 2.5.6 3.6.1.3 0 .7-.2 1z"/></svg>
        </p>
        <p class="contact__line contact__line--web">www.skylarkreelworks.example
          <svg viewBox="0 0 24 24" aria-hidden="true"><circle cx="12" cy="12" r="10" fill="none" stroke="#ec8a52" stroke-width="2"/><path d="M2 12h20M12 2c3 3 3 17 0 20M12 2c-3 3-3 17 0 20" fill="none" stroke="#ec8a52" stroke-width="1.6"/></svg>
        </p>
      </div>
    </div>
  </section>
</main>
</body>
</html>
```